Website and Mobile Devices design for food related application.

We need a design that is simple yet playful. The design should be food related if possible.
This design will be on the website and the mobile platform markets we intend application to be deployed too.
This application/website is called "Forkwizo[.com]. Its a random restaurant picker for the indecisive users.
Updates
Hi all, I picked a design. Again lots of great designs were submitted but I picked one that was more in line with what I wanted.
Target Market(s)
young internet savvy users.
Industry/Entity Type
Restaurant
Look and feel
Each slider illustrates characteristics of the customer's brand and the style your logo design should communicate.

```html
<!DOCTYPE html>
<html lang="en">
<head>
<meta charset="utf-8">
<title>Forkwizo – Reservation flow</title>
<link rel="stylesheet" href="https://fonts.googleapis.com/css2?family=Arimo:wght@400;700&family=PT+Sans:wght@400;700&display=swap">
<style>
  :root {
    --page-bg: #cfdde3;
    --status-bg: #0c0c0c;
    --nav-bg: #2a2a2a;
    --nav-text: #c9c9c9;
    --screen-top: #3fb5d2;
    --screen-mid: #46c3d3;
    --screen-bottom: #3a82c4;
    --white: #ffffff;
    --accent-red: #d42a2a;
    --tab-bg: #1d1d1d;
    --tab-active: #3a3a3a;
    --tab-text: #b5b5b5;
    --dialog-frame: #a9d0da;
    --dialog-bg: #a14d55;
    --picker-dark: #1f5c6c;
    --picker-light: #47bfcc;
    --picker-select: rgba(150, 110, 170, 0.75);
  }
  * { box-sizing: border-box; margin: 0; padding: 0; }
  html, body { width: 1200px; height: 1000px; overflow: hidden; }
  body {
    background: var(--page-bg);
    font-family: "PT Sans", sans-serif;
    position: relative;
  }
  .screen {
    position: absolute;
    top: 350px;
    width: 282px;
    height: 422px;
    overflow: hidden;
    background: var(--status-bg);
  }
  .screen--picker { left: 51px; }
  .screen--identity { left: 459px; }
  .screen--done { left: 871px; }

  .status-bar {
    height: 18px;
    display: flex;
    align-items: center;
    justify-content: space-between;
    padding: 0 6px;
    color: var(--white);
    font-family: "Arimo", sans-serif;
    font-weight: 700;
    font-size: 11px;
  }
  .status-bar__carrier { display: flex; align-items: center; gap: 3px; }
  .status-bar__time { font-size: 13px; }

  .nav-bar {
    height: 37px;
    background: linear-gradient(#3a3a3a, #232323);
    color: var(--nav-text);
    font-family: "Arimo", sans-serif;
    font-size: 17px;
    text-align: center;
    line-height: 37px;
  }

  .content {
    position: relative;
    height: 328px;
    background: linear-gradient(180deg, var(--screen-top) 0%, var(--screen-mid) 40%, var(--screen-bottom) 100%);
    text-align: center;
  }
  .restaurant-name {
    position: absolute; top: 14px; left: 0; right: 0;
    color: var(--white); font-size: 19px;
  }
  .restaurant-cuisine {
    position: absolute; top: 35px; left: 0; right: 0;
    color: var(--accent-red); font-size: 13px;
  }

  .picker-labels {
    position: absolute; top: 90px; left: 37px; width: 203px;
    display: flex; justify-content: space-around;
    color: var(--accent-red); font-family: "Arimo", sans-serif; font-size: 10px;
  }
  .picker {
    position: absolute; top: 109px; left: 37px; width: 203px; height: 103px;
    display: flex; gap: 2px;
    background: #6a2a44;
    border: 1px solid #274a55;
    overflow: hidden;
  }
  .picker__column {
    flex: 1;
    background: linear-gradient(180deg, var(--picker-dark) 0%, var(--picker-light) 30%, var(--picker-light) 70%, var(--picker-dark) 100%);
    font-family: "Arimo", sans-serif; font-weight: 700; font-size: 13px;
    color: var(--white);
    padding-top: 0;
  }
  .picker__row { height: 23px; line-height: 23px; }
  .picker__row--faded { color: rgba(255,255,255,0.35); }
  .picker__row--selected { color: rgba(255,255,255,0.55); }
  .picker__selection {
    position: absolute; top: 39px; left: 0; right: 0; height: 23px;
    background: var(--picker-select);
    border-top: 1px solid rgba(255,255,255,0.5);
    border-bottom: 1px solid rgba(60,20,60,0.6);
  }
  .picker__edge {
    position: absolute; left: 0; right: 0; height: 3px; top: -3px;
  }

  .reserve-link {
    position: absolute; top: 287px; left: 0; right: 0;
    color: #e6f4f8; font-family: "Arimo", sans-serif; font-size: 12px;
  }
  .reserve-link__arrow { color: var(--accent-red); font-weight: 700; margin-left: 6px; }

  .dialog {
    position: absolute; top: 110px; left: 36px; width: 212px; height: 117px;
    background: var(--dialog-frame);
    padding: 5px;
  }
  .dialog__body {
    width: 100%; height: 100%;
    background: var(--dialog-bg);
    border-radius: 4px;
    border: 1px solid #c97e86;
    position: relative;
    color: var(--white);
    font-family: "Arimo", sans-serif;
  }
  .dialog__title { position: absolute; top: 16px; left: 0; right: 0; font-size: 10px; }
  .dialog__hint { position: absolute; top: 40px; left: 0; right: 0; font-size: 9px; }
  .dialog__field {
    position: absolute; top: 55px; left: 10px; right: 10px; height: 16px;
    background: var(--white); border: 1px solid #ddd;
  }
  .dialog__actions {
    position: absolute; top: 84px; right: 10px; display: flex; gap: 6px;
  }
  .dialog__button {
    width: 48px; height: 13px;
    background: linear-gradient(#e9f6fa, #9ed3e2);
    border: 1px solid #6aa6b8;
    color: #1a1a1a; font-size: 7px; line-height: 11px; text-align: center;
  }

  .reserved-label {
    position: absolute; top: 212px; left: 0; right: 0;
    color: var(--accent-red); font-size: 17px;
  }

  .tab-bar {
    height: 39px;
    background: linear-gradient(#2a2a2a, #141414);
    display: flex;
    padding: 0 2px;
  }
  .tab {
    flex: 1;
    display: flex; flex-direction: column; align-items: center; justify-content: flex-end;
    padding-bottom: 3px;
    color: var(--tab-text);
    font-family: "Arimo", sans-serif; font-size: 8px;
    gap: 2px;
  }
  .tab svg { width: 15px; height: 15px; fill: var(--white); }
  .tab--active { background: var(--tab-active); color: var(--accent-red); font-weight: 700; }
</style>
</head>
<body>

<!-- Step 1: choose diners, time and date -->
<section class="screen screen--picker">
  <div class="status-bar">
    <span class="status-bar__carrier">
      <svg width="12" height="7" viewBox="0 0 12 7" fill="#fff"><rect x="0" y="5" width="2" height="2"/><rect x="2.5" y="4" width="2" height="3"/><rect x="5" y="3" width="2" height="4"/><rect x="7.5" y="1.5" width="2" height="5.5"/><rect x="10" y="0" width="2" height="7"/></svg>
      Mobile
    </span>
    <span class="status-bar__time">6:40 PM</span>
    <svg width="18" height="8" viewBox="0 0 18 8"><rect x="0.5" y="0.5" width="15" height="7" fill="none" stroke="#fff"/><rect x="2" y="2" width="12" height="4" fill="#fff"/><rect x="16" y="2.5" width="1.5" height="3" fill="#fff"/></svg>
  </div>
  <header class="nav-bar">Reservation</header>
  <main class="content">
    <h1 class="restaurant-name">Name Of Restaurant 2</h1>
    <p class="restaurant-cuisine">French</p>
    <div class="picker-labels"><span>Diners</span><span>Time</span><span>Date</span></div>
    <div class="picker">
      <div class="picker__selection"></div>
      <div class="picker__column">
        <div class="picker__row picker__row--faded">&nbsp;</div>
        <div class="picker__row">0</div>
        <div class="picker__row picker__row--selected">1</div>
        <div class="picker__row">2</div>
        <div class="picker__row picker__row--faded">3</div>
      </div>
      <div class="picker__column">
        <div class="picker__row picker__row--faded">19.00</div>
        <div class="picker__row">19.30</div>
        <div class="picker__row picker__row--selected">20.00</div>
        <div class="picker__row">20.30</div>
        <div class="picker__row picker__row--faded">21.00</div>
      </div>
      <div class="picker__column">
        <div class="picker__row picker__row--faded">19/07</div>
        <div class="picker__row">20/07</div>
        <div class="picker__row picker__row--selected">21/07</div>
        <div class="picker__row">22/07</div>
        <div class="picker__row picker__row--faded">23/07</div>
      </div>
    </div>
    <p class="reserve-link">Reservate<span class="reserve-link__arrow">›</span></p>
  </main>
  <nav class="tab-bar">
    <div class="tab"><svg viewBox="0 0 16 16"><path d="M8 0a5 5 0 0 0-5 5c0 4 5 11 5 11s5-7 5-11a5 5 0 0 0-5-5zm0 7a2 2 0 1 1 0-4 2 2 0 0 1 0 4z"/></svg>Stations</div>
    <div class="tab"><svg viewBox="0 0 16 16"><circle cx="7" cy="5" r="4"/><path d="M6 8l2 1-3 6-1-1z"/></svg>Map</div>
    <div class="tab"><svg viewBox="0 0 16 16"><path d="M8 0l2.4 5 5.6.6-4.2 3.8 1.2 5.6L8 12.2 3 15l1.2-5.6L0 5.6 5.6 5z"/></svg>Favoris</div>
    <div class="tab tab--active"><svg viewBox="0 0 16 16"><rect x="0" y="3" width="16" height="10" rx="1"/><rect x="0" y="5" width="16" height="2" fill="#3a3a3a"/></svg>Reservation</div>
    <div class="tab"><svg viewBox="0 0 16 16"><path d="M3 1l3 3-1.5 2a9 9 0 0 0 5.5 5.5L12 10l3 3-2 2C7 15 1 9 1 3z"/></svg>Contact</div>
  </nav>
</section>

<!-- Step 2: identity -->
<section class="screen screen--identity">
  <div class="status-bar">
    <span class="status-bar__carrier">
      <svg width="12" height="7" viewBox="0 0 12 7" fill="#fff"><rect x="0" y="5" width="2" height="2"/><rect x="2.5" y="4" width="2" height="3"/><rect x="5" y="3" width="2" height="4"/><rect x="7.5" y="1.5" width="2" height="5.5"/><rect x="10" y="0" width="2" height="7"/></svg>
      Mobile
    </span>
    <span class="status-bar__time">6:40 PM</span>
    <svg width="18" height="8" viewBox="0 0 18 8"><rect x="0.5" y="0.5" width="15" height="7" fill="none" stroke="#fff"/><rect x="2" y="2" width="12" height="4" fill="#fff"/><rect x="16" y="2.5" width="1.5" height="3" fill="#fff"/></svg>
  </div>
  <header class="nav-bar">Reservation</header>
  <main class="content">
    <h1 class="restaurant-name">Name Of Restaurant 2</h1>
    <p class="restaurant-cuisine">French</p>
    <div class="dialog">
      <div class="dialog__body">
        <p class="dialog__title">Identity</p>
        <p class="dialog__hint">name-name@mailbox.net</p>
        <div class="dialog__field"></div>
        <div class="dialog__actions">
          <span class="dialog__button">Annuler</span>
          <span class="dialog__button">OK</span>
        </div>
      </div>
    </div>
  </main>
  <nav class="tab-bar">
    <div class="tab"><svg viewBox="0 0 16 16"><path d="M8 0a5 5 0 0 0-5 5c0 4 5 11 5 11s5-7 5-11a5 5 0 0 0-5-5zm0 7a2 2 0 1 1 0-4 2 2 0 0 1 0 4z"/></svg>Stations</div>
    <div class="tab"><svg viewBox="0 0 16 16"><circle cx="7" cy="5" r="4"/><path d="M6 8l2 1-3 6-1-1z"/></svg>Map</div>
    <div class="tab"><svg viewBox="0 0 16 16"><path d="M8 0l2.4 5 5.6.6-4.2 3.8 1.2 5.6L8 12.2 3 15l1.2-5.6L0 5.6 5.6 5z"/></svg>Favoris</div>
    <div class="tab tab--active"><svg viewBox="0 0 16 16"><rect x="0" y="3" width="16" height="10" rx="1"/><rect x="0" y="5" width="16" height="2" fill="#3a3a3a"/></svg>Reservation</div>
    <div class="tab"><svg viewBox="0 0 16 16"><path d="M3 1l3 3-1.5 2a9 9 0 0 0 5.5 5.5L12 10l3 3-2 2C7 15 1 9 1 3z"/></svg>Contact</div>
  </nav>
</section>

<!-- Step 3: confirmation -->
<section class="screen screen--done">
  <div class="status-bar">
    <span class="status-bar__carrier">
      <svg width="12" height="7" viewBox="0 0 12 7" fill="#fff"><rect x="0" y="5" width="2" height="2"/><rect x="2.5" y="4" width="2" height="3"/><rect x="5" y="3" width="2" height="4"/><rect x="7.5" y="1.5" width="2" height="5.5"/><rect x="10" y="0" width="2" height="7"/></svg>
      Mobile
    </span>
    <span class="status-bar__time">6:40 PM</span>
    <svg width="18" height="8" viewBox="0 0 18 8"><rect x="0.5" y="0.5" width="15" height="7" fill="none" stroke="#fff"/><rect x="2" y="2" width="12" height="4" fill="#fff"/><rect x="16" y="2.5" width="1.5" height="3" fill="#fff"/></svg>
  </div>
  <header class="nav-bar">Reservation</header>
  <main class="content">
    <h1 class="restaurant-name">Name Of Restaurant 2</h1>
    <p class="restaurant-cuisine">French</p>
    <p class="reserved-label">Reserved</p>
  </main>
  <nav class="tab-bar">
    <div class="tab"><svg viewBox="0 0 16 16"><path d="M8 0a5 5 0 0 0-5 5c0 4 5 11 5 11s5-7 5-11a5 5 0 0 0-5-5zm0 7a2 2 0 1 1 0-4 2 2 0 0 1 0 4z"/></svg>Stations</div>
    <div class="tab"><svg viewBox="0 0 16 16"><circle cx="7" cy="5" r="4"/><path d="M6 8l2 1-3 6-1-1z"/></svg>Map</div>
    <div class="tab"><svg viewBox="0 0 16 16"><path d="M8 0l2.4 5 5.6.6-4.2 3.8 1.2 5.6L8 12.2 3 15l1.2-5.6L0 5.6 5.6 5z"/></svg>Favoris</div>
    <div class="tab tab--active"><svg viewBox="0 0 16 16"><rect x="0" y="3" width="16" height="10" rx="1"/><rect x="0" y="5" width="16" height="2" fill="#3a3a3a"/></svg>Reservation</div>
    <div class="tab"><svg viewBox="0 0 16 16"><path d="M3 1l3 3-1.5 2a9 9 0 0 0 5.5 5.5L12 10l3 3-2 2C7 15 1 9 1 3z"/></svg>Contact</div>
  </nav>
</section>

</body>
</html>
```